Design a book cover
TItle: Where Would Mercy Stand?
Suggested graphic: Jesus holding a gun
Subtitle: A Trial Lawyer's Reflections on Capital Justice
Author Name: Gordon Maskelyne

```html
<!DOCTYPE html>
<html lang="en">
<head>
<meta charset="utf-8">
<title>Where Would Mercy Stand? — Book Cover</title>
<link rel="stylesheet" href="https://fonts.googleapis.com/css2?family=Oswald:wght@400;500&family=Libre+Baskerville&display=swap">
<style>
  :root {
    --page-bg: #ecebe8;
    --cover-blue: #56658b;
    --cover-blue-light: #63729a;
    --title-white: #ffffff;
    --subtitle-ink: #e6e8f0;
    --rule-gold: #b8a36a;
    --art-cream: #d9cfae;
    --art-dark: #2a2c33;
  }
  * { margin: 0; padding: 0; box-sizing: border-box; }
  html, body {
    width: 1200px;
    height: 730px;
    overflow: hidden;
    background: var(--page-bg);
  }
  .stage {
    width: 1200px;
    height: 730px;
    display: flex;
    align-items: center;
    justify-content: center;
  }
  .book-cover {
    position: relative;
    width: 440px;
    height: 664px;
    background: linear-gradient(180deg, var(--cover-blue) 0%, var(--cover-blue-light) 100%);
    box-shadow: 0 6px 18px rgba(0, 0, 0, 0.18);
    display: flex;
    flex-direction: column;
    align-items: center;
  }
  .book-title {
    margin-top: 36px;
    font-family: "Oswald", sans-serif;
    font-weight: 500;
    font-size: 54px;
    line-height: 1.12;
    letter-spacing: 2px;
    text-transform: uppercase;
    color: var(--title-white);
    text-align: center;
  }
  .book-subtitle {
    margin-top: 22px;
    width: 300px;
    padding: 8px 0 10px;
    border-top: 1px solid var(--rule-gold);
    border-bottom: 1px solid var(--rule-gold);
    font-family: "Libre Baskerville", serif;
    font-size: 12px;
    line-height: 1.55;
    letter-spacing: 1px;
    text-transform: uppercase;
    color: var(--subtitle-ink);
    text-align: center;
  }
  .cover-art {
    margin-top: 26px;
    width: 260px;
    height: 220px;
    display: block;
  }
  .author-name {
    margin-top: auto;
    margin-bottom: 68px;
    font-family: "Oswald", sans-serif;
    font-weight: 400;
    font-size: 30px;
    letter-spacing: 4px;
    text-transform: uppercase;
    color: var(--title-white);
  }
</style>
</head>
<body>
  <main class="stage">
    <section class="book-cover">
      <h1 class="book-title">Where Would<br>Mercy Stand?</h1>
      <p class="book-subtitle">A trial lawyer's reflections<br>on capital justice</p>
      <svg class="cover-art" viewBox="0 0 260 220" role="img" aria-label="Photograph of a crucifix lying beside a handgun with three bullets">
        <defs>
          <linearGradient id="art-tones" x1="0" y1="0" x2="1" y2="0">
            <stop offset="0" stop-color="var(--art-cream)" stop-opacity="0.55"/>
            <stop offset="1" stop-color="var(--art-dark)" stop-opacity="0.55"/>
          </linearGradient>
        </defs>
        <rect x="0" y="0" width="260" height="220" rx="6" fill="url(#art-tones)"/>
      </svg>
      <p class="author-name">Gordon Maskelyne</p>
    </section>
  </main>
</body>
</html>
```